I need a logo design for a new company based in Tucson called "Mindtrail Lee Corwin". I am a psychotherapist that specializes in clinical psychology with athletes and performers. The final design should incorporate the psychology symbol as a watermark. The logo should convey movement and fluidity. "Mindtrail" is a bit of a play on words combining psychology (head) with sports (coach). Other design interests include mid-century, Harold Ames Whitby. I will want to use the logo for business cards, letterhead and marketing brochures. I will put together a website at a later date. I am attaching a file with some pertinent information for the business card. Thank you.
Lee Corwin
mindtrailleecorwin@quillpost.net

Thank you all for the submissions so far.  I have submitted an additional file with a draft of a new design idea.  Since "mindtrail" is a bit of a play on words, I would like to see something with the two "H's" look something like quotation marks.  If the psychology logo is to be included at all, it needs to be less prominent.     Thank you all.  Lee                               

Target Market(s)

1) Adolescent and adult athletes and performers who are looking to increase their level of performance (Sport and Performance Psychology)
2) Adult psychotherapy patients (Clinical psychology)

Industry/Entity Type

Marketing

Colors

Designer to choose colors to be used in the design.

Requirements
Must have
• 1) Since "mindtrail" is a bit of a play on words, The "H's" need to be in a font that looks somewhat like quotation marks.

Nice to have
• Logo on one side. All other info on the backside?

```html
<!DOCTYPE html>
<html lang="en">
<head>
<meta charset="utf-8">
<title>Mindtrail – Business Card</title>
<link rel="stylesheet" href="https://fonts.googleapis.com/css2?family=Alegreya:wght@400;700&family=Open+Sans:wght@400;600&display=swap">
<style>
  :root {
    --page-bg: #e9e7e3;
    --card-bg: #1e1e1e;
    --card-edge: #111111;
    --teal: #7cbdb2;
    --white: #f4f4f4;
    --field: #ffffff;
  }
  * { box-sizing: border-box; margin: 0; padding: 0; }
  html, body {
    width: 1200px;
    height: 1000px;
    overflow: hidden;
    background: var(--page-bg);
  }
  .canvas {
    position: relative;
    width: 1200px;
    height: 1000px;
  }
  .card {
    position: absolute;
    left: 250px;
    width: 700px;
    height: 400px;
    background: var(--card-bg);
    border-radius: 22px;
    box-shadow: 0 6px 0 var(--card-edge), 0 14px 30px rgba(0,0,0,0.25);
    color: var(--white);
    overflow: hidden;
  }
  .card-front { top: 60px; }
  .card-back { top: 530px; }

  /* Front */
  .brand {
    position: absolute;
    left: 0; right: 0; top: 110px;
    text-align: center;
  }
  .brand-name {
    display: inline-flex;
    align-items: center;
    gap: 22px;
    font-family: "Alegreya", serif;
    font-weight: 700;
    font-size: 104px;
    line-height: 1;
    color: var(--teal);
  }
  .brand-mark {
    width: 26px;
    height: 26px;
    border-radius: 50%;
    background: var(--teal);
  }
  .brand-tagline {
    margin-top: 26px;
    font-family: "Open Sans", sans-serif;
    font-weight: 400;
    font-size: 25px;
    letter-spacing: 1.5px;
    color: var(--white);
  }

  /* Back */
  .contact {
    position: absolute;
    left: 46px;
    top: 40px;
    width: 420px;
  }
  .person-name {
    font-family: "Alegreya", serif;
    font-weight: 400;
    font-size: 40px;
    line-height: 1.05;
    color: var(--teal);
    white-space: nowrap;
  }
  .person-title {
    margin-top: 6px;
    margin-left: 4px;
    font-family: "Open Sans", sans-serif;
    font-size: 18px;
    color: var(--white);
  }
  .details {
    list-style: none;
    margin-top: 40px;
    margin-left: 4px;
    font-family: "Open Sans", sans-serif;
    font-size: 16.5px;
    line-height: 1.6;
    color: var(--white);
    white-space: nowrap;
  }
  .details .label { color: var(--teal); }

  .appointment {
    position: absolute;
    right: 36px;
    top: 150px;
    width: 180px;
    font-family: "Alegreya", serif;
    color: var(--teal);
  }
  .appointment-title {
    text-align: center;
    font-size: 22px;
    letter-spacing: 1px;
    margin-bottom: 20px;
  }
  .field {
    display: flex;
    align-items: center;
    gap: 10px;
    margin-bottom: 20px;
    font-size: 21px;
  }
  .field-label { width: 52px; }
  .field-box {
    flex: 1;
    height: 46px;
    background: var(--field);
  }
</style>
</head>
<body>
<main class="canvas">

  <section class="card card-front" aria-label="Card front">
    <div class="brand">
      <div class="brand-name"><span class="brand-mark"></span>Mindtrail</div>
      <p class="brand-tagline">CLINICAL &amp; PERFORMANCE PSYCHOLOGY</p>
    </div>
  </section>

  <section class="card card-back" aria-label="Card back">
    <div class="contact">
      <h1 class="person-name">Lee H. Corwin, MA, LLC</h1>
      <p class="person-title">Licensed Professional Counselor</p>
      <ul class="details">
        <li><span class="label">Fax:</span> 520.555.0147</li>
        <li><span class="label">Mobile:</span> 520.555.0182</li>
        <li><span class="label">Email:</span> mindtrailleecorwin@quillpost.net</li>
        <li><span class="label">Address:</span> 4410 East Sabino #210 Tucson, AZ 85718</li>
      </ul>
    </div>

    <div class="appointment">
      <p class="appointment-title">APPOINTMENT</p>
      <div class="field"><span class="field-label">Date:</span><span class="field-box"></span></div>
      <div class="field"><span class="field-label">Time:</span><span class="field-box"></span></div>
    </div>
  </section>

</main>
</body>
</html>
```